Folder and brochures for food service software solution

We offer integrated software solutions for independent and chain food service businesses. Such businesses would include fine dining restaurants, fast food outlets, home delivery, takeaways, cafeterias, event catering venues, institutional catering companies, hotels with restaurants / bars, etc. Our software is configured for the needs of each type of business and spans both guest facing and back office functions.

The core benefits our solution offers is that it is -
1. integrated to cater to all the needs of the food service business, both independent and chain, across most (not all, we do not do anything for labor management) functions.
2. functionally powerful and compare well with the best available internationally.
3. Developed using the latest in software technology ... for example, our EPOS software for Pocketa devices.

The market is a mature market with many competitors. A few very well established with huge track record. We have a track record internationally but are new to the UK market. This brochure is targeted at the UK market. The target market is jaded with the number of options available. We will focus on fine dining outlets in the hope that our Pocketa based EPOS will excite them. We will focus on events & catering because the competition in the segment is relatively thin. We will go after the institutional catering market because we offer strong cost control features. But we want to mention how we service all sub-segments of the food & beverage service business to convey the versatility of our solution and for the other businesses that we may be able to attract.

We are hoping that the brochure will stand-out from the crowd and will compel the market to browse through what we do.

Some key competitors in the UK include -
http://www.venbrook.co.uk/
http://www.q-til.co.uk/
http://www.harromax.co.uk/
http://dunvey.co.uk/

We have a company and product logo (both attached). Of these, we are open to dropping or redesgning the product logo. We have also developed a web site (see kbuk.tarvensystems.example). The brochure design need not conform to the web site, if (and only if) you can come up with a really attention design (we could consider redesign of the web site).

The content of the brochure will largely conform to the content at the web site. The content at the web site is structured by solutions for independent outlets (centered around the EPOS) and solutions for chains. It also mentions 18 products. This is too much for a print brochure. So, we propose the following structure -

1. a folder that also carries a brief about our company with facility to add inserts.
2. one brochure that describes the solutions offered, the market segments they apply to and the benefits of the solution for each segment.
3. A summary / list of the products that are used to configure the solution.

We will add product specific flyers to the folder by color laser printing these. This will provide us the flexibility to add only the few product sheets that are of relevance to each prospect and will allow us to update frequently. For this we will require a template so that all product sheets look similar ... possibly with a color theme separating the products for each outlet from those for the chain of outlets.

We can only provide low-res images. You will have to touch up screens to improve resolution of images to make them print-ready. You are free to propose purchase of reasonably priced general stock-shots subject to prior approval from us. We will pay for these images.
Updates

At least one of you have requested that we -

1. identify a key message and

2. compact the contents of the brochure 

To do so, we have had to take an alternative approach and revise the content completely. Please check back and see the latest uploads, both Marlo - Approach 2 and Marlo - Salient Features.

We hope this helps you in your design effort.                     

Reason: We understand that we are requesting this design through a holiday season. We are extending the deadline by a few days. If this also does not work for some of you, please let us know a realistic date by which you are able to provide us options. We will consider, even though we are on a tight time line.

Reason: Some of you are still working on final layouts At least one of you is waiting for us to provide you modified content to fit the design. The extra days are intended to allow you to provide a complete and final design.

Earlier, we had posted an update and new content. This was in response to the community's request to reduce content. Did you note that? It seems not. So, we have now removed older content and only retained the revised content as per the last update. Please verify that the design you propose is as per the latest content. In the process, we may have removed some images also. Need them? Let me know and I will re-post.

Reason: Further extension, open only to those that have previously submitted designs and need the extra time to finalize the design based on feedback from us.

Target Market(s)

Upper mid market fine dining restaurants, likely with home delivery / takeaway options.
Small food service chains (3 to 10 outlets).
Venues with catering facilities.
Cafeterias.
Bulk food suppliers / institutional caterers.
Food service business with a central kitchen / commissary and multiple service locations.
membership clubs with food service.

Industry/Entity Type

Software

Font styles to use
Sans Serif

Requirements
Must have
• A distinctive attention grabbing design.

The structure of -
1. a folder with facility for inserts.
2. two brochures.
3. template for product specific write-ups.
Nice to have
• Info-graphics to represent an integrated solution. Another to demonstrate versatility across types of F&B business.

A design that relates the solution to the UK ... either in terms of colors or visuals.

```html
<!DOCTYPE html>
<html lang="en">
<head>
<meta charset="utf-8">
<title>Marlo – Sector Benefits</title>
<link href="https://fonts.googleapis.com/css2?family=Exo+2:wght@600;700&family=Open+Sans:wght@300;400&display=swap" rel="stylesheet">
<style>
  :root {
    --brand-red: #d71920;
    --brand-red-dark: #a8101a;
    --brand-red-light: #ec3a3f;
    --heading-red: #c8161d;
    --text-dark: #3a3a3a;
    --page-top: #ffffff;
    --page-bottom: #e6e6e6;
    --white: #ffffff;
  }
  * { margin: 0; padding: 0; box-sizing: border-box; }
  html, body { width: 841px; height: 1200px; overflow: hidden; }
  body {
    position: relative;
    background: linear-gradient(180deg, var(--page-top) 0%, #f3f3f3 55%, var(--page-bottom) 100%);
    font-family: "Open Sans", Arial, sans-serif;
    color: var(--text-dark);
  }
  .intro-band {
    position: absolute; left: 0; top: 0; width: 841px; height: 145px;
  }
  .intro-band svg { position: absolute; inset: 0; }
  .intro-text {
    position: absolute; left: 60px; top: 16px; width: 721px;
    text-align: center; color: var(--white);
    font-weight: 300; font-size: 24px; line-height: 29px;
  }
  .sector { position: absolute; left: 0; width: 841px; }
  .sector-visual { position: absolute; left: 0; top: 0; }
  .sector-body { position: absolute; left: 329px; width: 490px; }
  .sector-title {
    font-family: "Exo 2", Arial, sans-serif; font-weight: 700;
    font-size: 29px; line-height: 32px; color: var(--heading-red);
    margin-bottom: 4px;
  }
  .benefits { list-style: none; }
  .benefits li {
    position: relative; padding-left: 9px;
    font-size: 12.6px; line-height: 15.4px; font-weight: 300;
  }
  .benefits li::before {
    content: ""; position: absolute; left: 0; top: 6px;
    width: 4px; height: 4px; background: var(--text-dark);
  }
</style>
</head>
<body>

<header class="intro-band">
  <svg width="841" height="145" viewBox="0 0 841 145">
    <defs>
      <linearGradient id="bandFill" x1="0" y1="0" x2="0" y2="1">
        <stop offset="0" stop-color="var(--brand-red-light)"/>
        <stop offset="1" stop-color="var(--brand-red)"/>
      </linearGradient>
    </defs>
    <polygon points="0,0 841,0 841,142 0,122" fill="var(--brand-red-dark)"/>
    <polygon points="0,0 841,0 841,128 0,116" fill="url(#bandFill)"/>
  </svg>
  <p class="intro-text">Marlo can be configured specifically for each type of food service business. In each case, it offers additional sector-specific benefits.</p>
</header>

<section class="sector" style="top:167px;">
  <svg class="sector-visual" style="top:16px;" width="310" height="208" viewBox="0 0 310 208" role="img" aria-label="Chef plating a fine dining dish">
    <defs><linearGradient id="fineFill" x1="0" y1="0" x2="1" y2="1"><stop offset="0" stop-color="#eeeae6"/><stop offset="0.6" stop-color="#c9a58c"/><stop offset="1" stop-color="#8a3a22"/></linearGradient></defs>
    <polygon points="0,0 283,0 262,208 0,208" fill="url(#fineFill)"/>
    <polygon points="290,0 310,0 288,208 268,208" fill="var(--brand-red)"/>
  </svg>
  <div class="sector-body">
    <h2 class="sector-title">Fine Dining</h2>
    <ul class="benefits">
      <li>Table Reservations module that helps optimal use of available tables through meal times. The table reservation system can be interfaced with a 3rd party table reservations portal of your choice.</li>
      <li>Table status is monitored allowing for further efficiency in table management.</li>
      <li>A repeat diner database that is valuable for direct marketing, guest recognition, personalization of guest services and customer profiling. For example, it can automatically add the guest’s known allergies to the KOT on the guest’s repeat visit.</li>
      <li>Order taking features such as course wise order taking for timely food preparation and cover wise order taking for improved table service.</li>
      <li>Automated application of discounts and promotions for loyalty and/or dining members.</li>
      <li>Personalized order taking at the table side.</li>
    </ul>
  </div>
</section>

<section class="sector" style="top:427px;">
  <svg class="sector-visual" style="top:2px;" width="310" height="208" viewBox="0 0 310 208" role="img" aria-label="Hotel key handed over at reception desk">
    <defs><linearGradient id="hotelFill" x1="0" y1="0" x2="1" y2="1"><stop offset="0" stop-color="#f2f0ee"/><stop offset="0.5" stop-color="#d9d2cc"/><stop offset="1" stop-color="#6a5c52"/></linearGradient></defs>
    <polygon points="0,0 283,0 262,208 0,208" fill="url(#hotelFill)"/>
    <polygon points="290,0 310,0 288,208 268,208" fill="var(--brand-red)"/>
  </svg>
  <div class="sector-body">
    <h2 class="sector-title">Hotels</h2>
    <ul class="benefits">
      <li>Multi-outlet table reservations module that allows a guest to call a single number to book a table at any of the outlets in a hotel.</li>
      <li>In room dining orders handling.</li>
      <li>Each POS station can handle multiple outlets.</li>
      <li>Take orders anywhere and print KOT instantly by using the cost-effective Pocketa mobile version of Marlo order taking.</li>
      <li>Add comments to the KOT so that Chef is informed about any special guest requests.</li>
      <li>Post checks to guest room account. Currently, Marlo is in use with Kestrel Systems’ HAVEN, Calyx and Vantor PMSs. It can be interfaced with any PMS that supports LXIS or HOTI interface standards.</li>
    </ul>
  </div>
</section>

<section class="sector" style="top:693px;">
  <svg class="sector-visual" width="310" height="208" viewBox="0 0 310 208" role="img" aria-label="Friends enjoying fast food at a counter">
    <defs><linearGradient id="qsrFill" x1="0" y1="0" x2="1" y2="1"><stop offset="0" stop-color="#5a3a24"/><stop offset="0.5" stop-color="#c48a5c"/><stop offset="1" stop-color="#3a2418"/></linearGradient></defs>
    <polygon points="0,0 283,0 262,208 0,208" fill="url(#qsrFill)"/>
    <polygon points="290,0 310,0 288,208 268,208" fill="var(--brand-red)"/>
  </svg>
  <div class="sector-body" style="top:20px;">
    <h2 class="sector-title">Quick Service / Fast Food</h2>
    <ul class="benefits">
      <li>Minimum key strokes for EPOS operations that makes guest handling fast.</li>
      <li>Point-of-purchase promotion through dual display at each EPOS station.</li>
      <li>More efficient food preparation by use of Kitchen Display Systems as alternative to KOT printers.</li>
      <li>Integration with loyalty system with instant redemption.</li>
      <li>Online inventory to track stocks of critical items and to initiate replenishment.</li>
    </ul>
  </div>
</section>

<section class="sector" style="top:949px;">
  <svg class="sector-visual" width="310" height="208" viewBox="0 0 310 208" role="img" aria-label="Card payment terminal held at a food court till">
    <defs><linearGradient id="courtFill" x1="0" y1="0" x2="1" y2="1"><stop offset="0" stop-color="#9a7a5a"/><stop offset="0.5" stop-color="#3a3a3e"/><stop offset="1" stop-color="#c9a888"/></linearGradient></defs>
    <polygon points="0,0 283,0 262,208 0,208" fill="url(#courtFill)"/>
    <polygon points="290,0 310,0 288,208 268,208" fill="var(--brand-red)"/>
  </svg>
  <div class="sector-body" style="top:6px;">
    <h2 class="sector-title">Food Courts</h2>
    <ul class="benefits">
      <li>All the benefits of QSR service, plus the option of cashless operations.</li>
      <li>Aggregate sales of all outlets for multi-outlet and/or consolidated reporting.</li>
    </ul>
  </div>
</section>

</body>
</html>
```